Web Design For Marlow Pool Service

We are working with a company that wants a website for their pool service. Some sites to use for content/competitors and inspiration:
https://sacramento.brightwaterpoolco.example/builder/newbuild/repair/ppc
https://hollowbrookpoolcareplus.example/
https://lakemontpoolservice.example/
https://www.dravenspoolresurfacing.example/pool-renovation-ga/
Thank you for taking the time to consider designing a website for us. We are web developers based in Stockton, CA, USA. Most of our projects go through the same process. Understanding this process may help you win a project with us. We custom-code all of our websites in-house. We don’t have any requirements as to what tools you use for your design, but we prefer Figma files. For any design that we label as four-stars, we send it to the client for review. The client picks the final design they want us to use. Once we complete this process, we will continue to show additional clients all the four-star sites and purchase them later. Your designs will have multiple chances to sell. For better chances of success, we ask that you follow these guidelines.
IMAGES:
If you use any images or icons in the design, we ask that you have a link to the asset so we can purchase the image/icon. Most of the designs we submit do not have the customer’s images on them unless they have some great images. Be creative; show us the feeling you are trying to portray with your image choices. Use any royalty-free site you choose. We subscribe to Adobe and mainly use their images, but we can purchase images outside of Adobe. PLEASE NOTE: we will not submit designs to clients with watermarks on the images.
FONTS:
We ask that you identify the fonts used in the design. This can be done in a message if you want. We typically use Google Fonts and Adobe Fonts.
CONTENT:
We're always open to different content and ideas. We often submit designs with stock images so the client can see our vision. We typically take pictures after the website launch to use their images with our vision. Lorem Ipsum is fine for paragraphs, but we ask that you write the headers in correct English. We want to be able to show the vision and identify the sections of the website.
INSPIRATION:
We typically add a couple of links in the brief of websites we like to help you get started in your design.
REVISIONS:
We do not often ask for revisions of the designs unless we see something in the design that may not appeal to the client. If there are slight changes that we want to make, we do that in the development process.
FEEDBACK:
We rarely give feedback on designs during the design process. We are working on many website projects and do not have the time to provide feedback. We usually respond if your request is well thought out and asks specific questions, but a note asking “feedback, please” usually goes unanswered.
Number of Pages Required
1 page
Look and feel
Each slider illustrates characteristics of the customer's brand and the style your logo design should communicate.

```html
<!DOCTYPE html>
<html lang="en">
<head>
<meta charset="utf-8">
<title>Marlow Pool Service</title>
<link rel="stylesheet" href="https://fonts.googleapis.com/css2?family=Open+Sans:wght@400;600;700&family=Fira+Sans:wght@500;600&display=swap">
<style>
:root{
  --blue:#2196f3;
  --navy:#163f72;
  --deep:#0d2342;
  --ink:#1f3a5f;
  --text:#555b63;
  --bg:#f5f5f5;
  --white:#ffffff;
  --footer:#1e2227;
  --star:#f0592a;
}
*{box-sizing:border-box;margin:0;padding:0}
html,body{width:1200px;height:4641px;overflow:hidden}
body{position:relative;background:var(--bg);font-family:"Open Sans",sans-serif;color:var(--text);font-size:13px}
.abs{position:absolute}
h1,h2,h3,.title{font-family:"Fira Sans",sans-serif;color:var(--ink);font-weight:600}
.btn{position:absolute;background:var(--blue);color:#fff;font-weight:700;font-size:12px;display:flex;align-items:center;justify-content:center;letter-spacing:.3px}
.section-title{position:absolute;left:0;width:1200px;text-align:center;font-size:31px}
.section-lead{position:absolute;left:300px;width:600px;text-align:center;line-height:22px;font-size:13px}

/* header */
.header{position:absolute;left:0;top:0;width:1200px;height:80px;z-index:2}
.header .bar{position:absolute;left:0;top:14px;width:1196px;height:66px;background:#fff}
.header .topline{position:absolute;left:420px;top:0;width:780px;height:28px;background:#fff;border-top-left-radius:20px;font-size:9px;color:#333}
.brand{position:absolute;left:120px;top:26px;display:flex;align-items:center;gap:8px;font-family:"Open Sans",sans-serif;font-weight:600;color:var(--blue);font-size:17px;letter-spacing:.5px}
.brand i{width:12px;height:12px;border-radius:50%;background:var(--blue);display:block}
.nav{position:absolute;top:50px;left:390px;display:flex;gap:0;font-size:11px;color:#444}
.nav span{width:92px;text-align:center}
.nav .active{color:var(--navy);font-weight:700}
.quote{position:absolute;left:842px;top:8px;width:112px;height:16px;border-bottom:4px solid var(--blue);color:var(--blue);font-size:9px;text-align:center}

/* hero */
.hero{position:absolute;left:0;top:0;width:1200px;height:763px;background:linear-gradient(180deg,#3f5364 0%,#7a7d78 40%,#8b7866 70%,#5d4d42 100%)}
.hero .welcome{position:absolute;left:111px;top:268px;color:#fff;font-size:13px;display:flex;align-items:center;gap:14px}
.hero .welcome b{width:44px;height:1px;background:#fff;display:block}
.hero h1{position:absolute;left:111px;top:296px;color:#fff;font-size:42px;line-height:58px;font-weight:600}
.hero p{position:absolute;left:111px;top:430px;width:420px;color:#fff;font-size:13px;line-height:21px}

/* why */
.cards4{position:absolute;top:970px;left:93px;display:flex;gap:28px}
.card4{width:233px;height:215px;background:#fff;box-shadow:0 2px 10px rgba(0,0,0,.07);text-align:center;padding-top:30px}
.card4 h3{font-size:19px;line-height:26px;margin-top:14px;height:56px;display:flex;align-items:center;justify-content:center}
.card4 p{font-size:12.5px;line-height:21px;padding:0 24px;margin-top:4px}
.card4.featured{background:var(--navy)}
.card4.featured h3,.card4.featured p{color:#fff}

/* crafting */
.craft-band{position:absolute;left:282px;top:1322px;width:918px;height:466px;background:var(--deep)}
.craft-photo{position:absolute;left:0;top:1384px;width:582px;height:449px;background:linear-gradient(135deg,#3c8ec9 0%,#6aaed6 30%,#a8a8a4 55%,#c04a3c 75%,#7a7a78 100%)}
.craft-band h2{position:absolute;left:350px;top:95px;color:#fff;font-size:30px}
.craft-band p{position:absolute;left:350px;width:450px;color:#e5ecf5;font-size:13px;line-height:22px}

/* what we do */
.services{position:absolute;top:2063px;left:93px;display:flex;gap:27px}
.service{position:relative;width:320px;height:380px}
.service .photo{position:absolute;left:0;top:0;width:320px;height:236px}
.service .panel{position:absolute;left:19px;top:177px;width:284px;height:203px;background:#fff;box-shadow:0 2px 10px rgba(0,0,0,.08);padding:22px 26px}
.service h3{font-size:21px;font-weight:500}
.service p{font-size:12.5px;line-height:22px;margin-top:8px}
.service .more{margin-top:6px;font-size:10.5px;font-weight:700;color:var(--blue)}
.service.featured .panel{background:var(--navy)}
.service.featured h3,.service.featured p,.service.featured .more{color:#fff}

/* cta */
.cta{position:absolute;left:0;top:2512px;width:1200px;height:298px;background:linear-gradient(180deg,#2e3440 0%,#4a4c50 55%,#26486a 100%);color:#fff;text-align:center}
.cta .phone{position:absolute;left:0;width:1200px;top:45px;display:flex;justify-content:center;align-items:center;gap:12px;font-family:"Fira Sans",sans-serif;font-size:22px;font-weight:600}
.cta h2{position:absolute;left:0;width:1200px;top:90px;color:#fff;font-size:31px}
.cta p{position:absolute;left:360px;width:480px;top:142px;line-height:22px}
.cta .ghost{position:absolute;left:518px;top:214px;width:172px;height:40px;border:2px solid #fff;display:flex;align-items:center;justify-content:center;font-size:11.5px;font-weight:700}

/* testimonials */
.quote-card{position:absolute;top:3038px;width:497px;height:260px;background:#eef0f2}
.quote-card .rule{position:absolute;left:62px;top:42px;width:2px;height:178px;background:#3a6ea5}
.quote-card .mark{position:absolute;left:37px;top:103px;width:52px;height:52px;border-radius:50%;background:var(--blue);border:4px solid #fff;box-shadow:0 0 0 2px var(--blue)}
.quote-card .stars{position:absolute;left:115px;top:40px;color:var(--star);font-size:17px;letter-spacing:4px}
.quote-card p{position:absolute;left:115px;top:90px;width:340px;line-height:22px}
.quote-card .name{position:absolute;left:115px;top:170px;font-size:17px;font-weight:600;color:#222}
.quote-card .place{position:absolute;left:115px;top:197px;font-size:12.5px}
.quote-card .avatar{position:absolute;left:400px;top:165px;width:58px;height:58px;border-radius:50%;background:linear-gradient(135deg,#c7b8a9,#6d5f55)}
.dots{position:absolute;top:3339px;left:563px;display:flex;gap:12px}
.dots i{width:10px;height:10px;border-radius:50%;background:#ddd;display:block}
.dots i.on{background:#fff;border:2px solid var(--star)}

/* contact */
.contact{position:absolute;left:91px;top:3596px;width:1014px;height:459px;background:#fff}
.contact .photo{position:absolute;left:0;top:0;width:510px;height:459px;background:linear-gradient(160deg,#23496d 0%,#356e95 50%,#1f3f60 100%)}
.contact .info{position:absolute;left:86px;top:70px;color:#fff;font-size:12px;line-height:18px}
.contact .info h4{font-size:16px;font-weight:600;margin-bottom:24px}
.contact .info .call{font-size:21px;margin-bottom:4px}
.social{display:flex;gap:12px;margin-top:36px}
.social i{width:30px;height:30px;border-radius:50%;background:rgba(255,255,255,.25);display:block}
.social i.on{background:#fff}
.form{position:absolute;left:596px;top:66px;width:333px}
.form h4{font-size:17px;color:var(--navy);font-weight:700;margin-bottom:32px}
.field{height:33px;background:#f3f3f3;margin-bottom:17px;font-size:10px;padding:10px 14px;color:#777}
.field.tall{height:94px}
.form .btn{position:relative;width:110px;height:37px}

/* info strip */
.strip{position:absolute;left:66px;top:4138px;width:1069px;height:104px;background:var(--blue);border-radius:8px;z-index:2;color:#fff}
.strip .item{position:absolute;top:26px;display:flex;gap:16px;align-items:center}
.strip b{display:block;font-size:17px;font-weight:700;margin-bottom:10px}
.strip span{font-size:12.5px}

/* footer */
.footer{position:absolute;left:0;top:4190px;width:1200px;height:451px;background:var(--footer);color:#ddd}
.footer h5{position:absolute;top:122px;color:#fff;font-size:18px;font-weight:700}
.footer .uline{position:absolute;top:158px;width:34px;height:2px;background:var(--blue)}
.footer .about{position:absolute;left:66px;top:190px;width:300px;font-size:13px;line-height:32px}
.footer .links{position:absolute;top:192px;font-size:13px;line-height:34px;text-decoration:underline}
.footer .readmore{color:#e07a4b;text-decoration:underline;font-size:15px}
.newsletter{position:absolute;left:797px;top:4497px;width:338px;height:56px;background:#fff;border-radius:4px;z-index:3}
.newsletter span{position:absolute;left:16px;top:20px;font-size:12px;color:#333}
.newsletter .go{position:absolute;right:0;top:0;width:64px;height:56px;background:var(--blue);border-radius:0 4px 4px 0;display:flex;align-items:center;justify-content:center}
.bottombar{position:absolute;left:0;top:4580px;width:1200px;height:1px;background:#3a3e44;z-index:3}
.foot-brand{position:absolute;left:66px;top:4578px;width:171px;height:63px;background:var(--blue);z-index:3;display:flex;align-items:center;justify-content:center;color:#fff;font-weight:600;font-size:15px}
.foot-social{position:absolute;left:897px;top:4580px;display:flex;z-index:3}
.foot-social i{width:60px;height:61px;border-left:1px solid #3a3e44;display:block}
</style>
</head>
<body>

<section class="hero" role="img" aria-label="Children jumping into a backyard pool at sunset">
</section>
<div class="hero" style="background:none">
  <div class="welcome">Welcome <b></b></div>
  <h1>Crafting Memories,<br>One Pool at a Time</h1>
  <p>Lorem ipsum dolor sit amet, consectetur adipiscing elit, sed do eiusmod tempor incididunt ut labore et dolore magna Lorem ipsum dolor sit amet, consectetur adipiscing elit, sed do eiusmod tempor incididunt ut labore et dolore magna</p>
  <div class="btn" style="left:111px;top:540px;width:192px;height:40px">Discover more</div>
</div>

<header class="header">
  <div class="bar"></div>
  <div class="topline">
    <span class="abs" style="left:46px;top:10px">&#9679; 48 Harbor Ln., Stockton, CA 95201</span>
    <span class="abs" style="left:283px;top:10px">Follow Us: &nbsp;&#9679; &#9679; &#9679;</span>
  </div>
  <div class="quote">GET QUOTATION</div>
  <div class="brand"><i></i>MARLOW POOL SERVICE</div>
  <nav class="nav"><span class="active">Home</span><span>About Us</span><span>Services</span><span>Gallery</span><span>Our Team</span><span>Contact Us</span></nav>
</header>

<!-- why -->
<h2 class="section-title" style="top:840px">Why We Are The Best</h2>
<p class="section-lead" style="top:893px">Lorem ipsum dolor sit amet, consectetur adipiscing elit, sed do eiusmod tempor incididunt ut labore et dolore magna aliqua. Ut enim ad min</p>
<div class="cards4">
  <div class="card4"><svg width="40" height="40" viewBox="0 0 40 40" fill="none" stroke="#2196f3" stroke-width="2"><circle cx="20" cy="20" r="6"/><circle cx="20" cy="20" r="14" stroke-dasharray="6 3"/></svg><h3>Expertise</h3><p>Lorem ipsum dolor sit amet, consectetur adipiscing</p></div>
  <div class="card4 featured"><svg width="40" height="40" viewBox="0 0 40 40" fill="none" stroke="#fff" stroke-width="2"><circle cx="20" cy="20" r="14"/><path d="M10 24h20M14 16h12"/></svg><h3>Comprehensive<br>Services</h3><p>Lorem ipsum dolor sit amet, consectetur adipiscing</p></div>
  <div class="card4"><svg width="40" height="40" viewBox="0 0 40 40" fill="none" stroke="#2196f3" stroke-width="2"><circle cx="20" cy="13" r="7"/><path d="M7 34c0-8 6-12 13-12s13 4 13 12z"/></svg><h3>Experienced</h3><p>Lorem ipsum dolor sit amet, consectetur adipiscing</p></div>
  <div class="card4"><svg width="40" height="40" viewBox="0 0 40 40" fill="none" stroke="#2196f3" stroke-width="2"><path d="M20 5l4.5 9.5 10.5 1.5-7.5 7.5 2 10.5-9.5-5-9.5 5 2-10.5L5 16l10.5-1.5z"/></svg><h3>Quality<br>Assurance</h3><p>Lorem ipsum dolor sit amet, consectetur adipiscing</p></div>
</div>
<div class="btn" style="left:521px;top:1225px;width:172px;height:40px">LEARN MORE ABOUT</div>

<!-- crafting -->
<section class="craft-band">
  <h2>Crafting Aquatic Masterpieces</h2>
  <p style="top:140px">Lorem ipsum dolor sit amet, consectetur adipiscing elit, sed do e iusmod tempor incididunt ut labore et dolore magna aliqua. Ut eni m ad minim veniam, quis nostrud ex</p>
  <p style="top:216px">Lorem ipsum dolor sit amet, consectetur adipiscing elit, sed do eius mod tempor incididunt ut labore et dolore magna aliqua. Ut enim a d minim veniam, quis nostrud exercitation ullamco laboris nisi ut aliq uip ex ea commodo consequat. Duis aute iru</p>
  <div class="btn" style="left:350px;top:330px;width:172px;height:40px;font-size:11.5px">LEARN MORE ABOUT</div>
</section>
<div class="craft-photo" role="img" aria-label="Technician in a red cap repairing pool equipment beside the water"></div>

<!-- what we do -->
<h2 class="section-title" style="top:1910px">What We Do</h2>
<p class="section-lead" style="top:1963px">Lorem ipsum dolor sit amet, consectetur adipiscing elit, sed do eiusmod tempor incididunt ut labore et dolore magna aliqua. Ut enim ad min</p>
<div class="services">
  <div class="service"><div class="photo" role="img" aria-label="Worker repairing pool tiles" style="background:linear-gradient(135deg,#6fa7cf,#3d7fb0 60%,#b9c7cf)"></div>
    <div class="panel"><h3>Pool Repair</h3><p>Lorem ipsum dolor sit amet, cons ectetur adipiscing elit, sed do eius mod tempor incididunt ut labore et dolore magna aliqua.</p><div class="more">LEARN MORE</div></div></div>
  <div class="service featured"><div class="photo" role="img" aria-label="Construction crew in hard hats on site" style="background:linear-gradient(135deg,#cfd3d6,#8e9aa3 60%,#5c6a72)"></div>
    <div class="panel"><h3>Pool Construction</h3><p>Lorem ipsum dolor sit amet, cons ectetur adipiscing elit, sed do eius mod tempor incididunt ut labore et dolore magna aliqua.</p><div class="more">LEARN MORE</div></div></div>
  <div class="service"><div class="photo" role="img" aria-label="Friends relaxing on floats in a clean pool" style="background:linear-gradient(135deg,#5c7a4a,#3fb3c9 55%,#a58b6e)"></div>
    <div class="panel"><h3>Pool Cleaning</h3><p>Lorem ipsum dolor sit amet, cons ectetur adipiscing elit, sed do eius mod tempor incididunt ut labore et dolore magna aliqua.</p><div class="more">LEARN MORE</div></div></div>
</div>

<!-- cta -->
<section class="cta" role="img" aria-label="Evening view of a modern home with an illuminated pool">
  <div class="phone"><svg width="34" height="34" viewBox="0 0 24 24" fill="none" stroke="#fff" stroke-width="1.4"><path d="M5 3h4l2 5-2.5 1.5a11 11 0 0 0 6 6L16 13l5 2v4a2 2 0 0 1-2 2A16 16 0 0 1 3 5a2 2 0 0 1 2-2z"/></svg>123-456-7890</div>
  <h2>Making Waves with Excellence</h2>
  <p>Lorem ipsum dolor sit amet, consectetur adipiscing elit, sed do eiusmod tempor incididunt ut labore et dolore magna aliqua.</p>
  <div class="ghost">CONTACT US NOW</div>
</section>

<!-- testimonials -->
<h2 class="section-title" style="top:2890px;left:-18px">Client Testimonials</h2>
<p class="section-lead" style="top:2943px;left:282px">Lorem ipsum dolor sit amet, consectetur adipiscing elit, sed do eiusmod tempor incididunt ut labore et dolore magna aliqua. Ut enim ad min</p>
<div class="quote-card" style="left:89px"><div class="rule"></div><div class="mark"></div><div class="stars">★★★★★</div><p>Lorem ipsum dolor sit amet, consectetur adipiscing elit, sed do eiusmod tempor incididunt ut labore et dolore magna aliqua. Ut enim</p><div class="name">Maren Holt</div><div class="place">Green Valley</div><div class="avatar" role="img" aria-label="Client portrait"></div></div>
<div class="quote-card" style="left:610px"><div class="rule"></div><div class="mark"></div><div class="stars">★★★★★</div><p>Lorem ipsum dolor sit amet, consectetur adipiscing elit, sed do eiusmod tempor incididunt ut labore et dolore magna aliqua. Ut enim</p><div class="name">Maren Holt</div><div class="place">Green Valley</div><div class="avatar" role="img" aria-label="Client portrait" style="background:linear-gradient(135deg,#e7d3b5,#b38d62)"></div></div>
<div class="dots"><i></i><i></i><i class="on"></i><i></i></div>

<!-- contact -->
<section style="position:absolute;left:0;top:3388px;width:1200px;height:1253px;background:#fff"></section>
<h2 class="section-title" style="top:3448px">Contact Us</h2>
<p class="section-lead" style="top:3501px">Lorem ipsum dolor sit amet, consectetur adipiscing elit, sed do eiusmod tempor incididunt ut labore et dolore magna aliqua. Ut enim ad min</p>
<div class="contact" style="box-shadow:0 0 0 1px #eee">
  <div class="photo" role="img" aria-label="Woman sitting at the edge of a pool"></div>
  <div class="info">
    <h4>CONTACT US</h4>
    <div class="call">Call: 0123456789</div>
    <div>info@company.com</div>
    <div style="margin-top:26px">Address:<br>SOME PLACE<br>51100 Road</div>
    <div style="margin-top:22px">Operating Hours<br>Monday to Saturday: 9:00 - 18:00<br>Sunday: Closed</div>
    <div class="social"><i></i><i class="on"></i><i></i><i></i></div>
  </div>
  <div class="form">
    <h4>FREE CONSULTATION</h4>
    <div class="field">Your Name</div>
    <div class="field">Email</div>
    <div class="field">Phone</div>
    <div class="field tall">Message ...</div>
    <div class="btn">SUBMIT</div>
  </div>
</div>

<!-- footer -->
<footer class="footer">
  <h5 style="left:66px">About Us</h5><div class="uline" style="left:66px"></div>
  <div class="about">Lorem ipsum dolor sit amet, consectetur adipi elit, sed do eiusmod tempor incididunt ut lab dolore magna aliqua.<br><span class="readmore">Read More</span></div>
  <h5 style="left:433px">Useful Links</h5><div class="uline" style="left:433px"></div>
  <div class="links" style="left:433px">About Us<br>Projects<br>Blog<br>Contact Us</div>
  <div class="links" style="left:611px">Services<br>Shop<br>Privacy Policy<br>Help Desk</div>
  <h5 style="left:797px">Useful Links</h5><div class="uline" style="left:797px"></div>
  <div class="abs" style="left:797px;top:194px;width:338px;font-size:14px;line-height:25px">If you have any questions, Subscribe to our newsletter to get our latest products</div>
</footer>
<div class="newsletter"><span>Email</span><div class="go"><svg width="22" height="22" viewBox="0 0 24 24" fill="none" stroke="#fff" stroke-width="2"><path d="M4 12h16M13 5l7 7-7 7"/></svg></div></div>
<div class="bottombar"></div>
<div class="foot-brand">MARLOW POOL SERVICE</div>
<div class="foot-social"><i></i><i></i><i></i><i></i><i style="border-right:1px solid #3a3e44"></i></div>

<div class="strip">
  <div class="item" style="left:40px"><svg width="52" height="52" viewBox="0 0 24 24" fill="none" stroke="#fff" stroke-width="1.2"><path d="M12 21s-6-6-6-11a6 6 0 0 1 12 0c0 5-6 11-6 11z"/><circle cx="12" cy="10" r="2.2"/><path d="M3 21h18"/></svg><div><b>Address</b><span>27, Sacramento, USA</span></div></div>
  <div class="item" style="left:396px"><svg width="52" height="52" viewBox="0 0 24 24" fill="none" stroke="#fff" stroke-width="1.2"><path d="M5 3h4l2 5-2.5 1.5a11 11 0 0 0 6 6L16 13l5 2v4a2 2 0 0 1-2 2A16 16 0 0 1 3 5a2 2 0 0 1 2-2z"/></svg><div><b>Phone</b><span>+123 456 78890</span></div></div>
  <div class="item" style="left:754px"><svg width="52" height="52" viewBox="0 0 24 24" fill="none" stroke="#fff" stroke-width="1.2"><rect x="3" y="8" width="18" height="13"/><path d="M3 8l9 7 9-7M7 5h10v6"/></svg><div><b>Email Contact</b><span>info@company.com</span></div></div>
</div>

</body>
</html>
```